Consulting Company PowerPoint Template Design

We are looking for an updated PowerPoint template design or our 55 person energy consulting firm (K7) based in San Francisco (www.kseven-example.com). We would like two versions of the same PowerPoint template in a 16:9 and 4:3 format with our existing logo.

We have an existing color scheme and template and are seeking your help to polish/update the template design for wide format and create a flexible template that is easy to use with content from Excel and Word. Our current template, and a couple of examples that we like are attached.

Specific requests include:

• Dark background for slide title
• A narrow section header
• Maximizing white space for content
• A limited number of well designed Master template layouts to choose from
• A selection of title and section header slides that are not San Francisco specific with some variety to chose from ideally with a focus on energy or nature, graphics/visuals.

For examples of energy specific templates see:
https://www.brightslidehub.example/energy/powerpoint-templates/0.html

Requirements
Must have
• Must use our logo but open to other designs, fonts, and styles for the PowerPoint template.
• Please use our existing color scheme found in the attached Excel file.
• Also we would like the ability to easily copy and paste from our existing/original template to the new template. In other words we would like backward compatibility to apply the new template format to our old PowerPoints that use our existing template.

```html
<!DOCTYPE html>
<html lang="en">
<head>
<meta charset="utf-8">
<title>K7 Problem Slide</title>
<link rel="stylesheet" href="https://fonts.googleapis.com/css2?family=Fira+Sans:wght@400;500;600&display=swap">
<style>
  :root {
    --navy: #064b6c;
    --gold: #d6b26b;
    --text-grey: #8c8c8c;
    --rule-grey: #d2d2d2;
    --white: #ffffff;
  }
  * { margin: 0; padding: 0; box-sizing: border-box; }
  html, body { width: 1200px; height: 900px; overflow: hidden; background: var(--white); }
  .slide {
    position: relative;
    width: 1200px;
    height: 900px;
    overflow: hidden;
    font-family: "Fira Sans", Arial, sans-serif;
    background: var(--white);
  }
  .slide-art { position: absolute; inset: 0; }
  .project-title {
    position: absolute;
    left: 18px;
    top: 12px;
    font-size: 31px;
    font-weight: 500;
    letter-spacing: 0.5px;
    color: var(--white);
  }
  .project-title .accent { color: var(--gold); }
  .brand-mark {
    position: absolute;
    left: 1111px;
    top: 3px;
    width: 78px;
    height: 78px;
    border-radius: 50%;
    background: var(--white);
    border: 4px solid var(--navy);
    display: flex;
    align-items: center;
    justify-content: center;
    font-size: 30px;
    font-weight: 600;
    color: var(--navy);
  }
  .problem {
    position: absolute;
    left: 576px;
    top: 380px;
    width: 570px;
  }
  .problem-title {
    font-size: 36px;
    font-weight: 500;
    color: var(--navy);
    letter-spacing: 0.3px;
    margin-bottom: 10px;
  }
  .problem-body {
    padding-left: 5px;
    font-size: 19px;
    line-height: 30px;
    color: var(--text-grey);
  }
  .problem-body p + p { margin-top: 30px; }
  .firm-name {
    position: absolute;
    left: 9px;
    top: 860px;
    font-size: 25px;
    font-weight: 500;
    color: var(--white);
  }
  .page-number {
    position: absolute;
    left: 1136px;
    top: 865px;
    font-size: 20px;
    color: var(--white);
  }
</style>
</head>
<body>
<main class="slide">
  <svg class="slide-art" width="1200" height="900" viewBox="0 0 1200 900" aria-hidden="true">
    <!-- header band -->
    <rect x="0" y="0" width="1200" height="66" fill="var(--navy)"/>
    <polygon points="0,66 1118,66 1108,75 0,75" fill="var(--gold)"/>
    <!-- diagonal guide -->
    <line x1="620" y1="230" x2="0" y2="850" stroke="var(--rule-grey)" stroke-width="1.5"/>
    <line x1="519" y1="332" x2="453" y2="398" stroke="var(--navy)" stroke-width="5"/>
    <line x1="275" y1="578" x2="210" y2="643" stroke="var(--navy)" stroke-width="5"/>
    <!-- icon circle -->
    <circle cx="363" cy="487" r="127" fill="var(--navy)"/>
    <g class="hourglass-icon" fill="none" stroke="var(--white)" stroke-width="3" stroke-linecap="round">
      <line x1="332" y1="446" x2="396" y2="446"/>
      <line x1="332" y1="527" x2="396" y2="527"/>
      <path d="M341 452 C341 472 356 478 360 486 C356 494 341 500 341 521"/>
      <path d="M387 452 C387 472 372 478 368 486 C372 494 387 500 387 521"/>
    </g>
    <g fill="var(--white)">
      <path d="M350 466 L378 466 C374 474 366 478 364 482 C362 478 354 474 350 466 Z"/>
      <circle cx="364" cy="492" r="1.5"/>
      <circle cx="364" cy="500" r="1.5"/>
      <circle cx="364" cy="508" r="1.5"/>
      <path d="M347 518 C352 510 360 508 364 508 C368 508 376 510 381 518 Z"/>
    </g>
    <!-- footer band -->
    <rect x="0" y="855" width="1200" height="45" fill="var(--navy)"/>
    <polygon points="1104,861 1200,861 1200,900 1122,900 1094,878" fill="var(--gold)"/>
  </svg>

  <h1 class="project-title"><span class="accent">PROJECT</span> TITLE HERE</h1>
  <div class="brand-mark">K7</div>

  <section class="problem">
    <h2 class="problem-title">YOUR PROBLEM TITLE HERE</h2>
    <div class="problem-body">
      <p>There are many variations of passages of Lorem Ipsum available, but the majority have suffered alteration in some form, by injected humour, or randomised words which don’t look even slightly believable. It is a long established fact that a reader will be distracted by the readable content of a page when looking at its layout.</p>
      <p>The point of using Lorem Ipsum is that it has a more-or-less normal distribution of letters, as opposed to using ‘Content here, content here’, making it look like readable English. Many desktop publishing packages and web page editors now use Lorem Ipsum</p>
    </div>
  </section>

  <footer>
    <div class="firm-name">Kinetic Seven Energy Advisors</div>
    <div class="page-number">01</div>
  </footer>
</main>
</body>
</html>
```